Google Form Graphic to suit our Brand and industry

Create a graphic / image for us to put at the top of our client enquiry google form.
The image will be a section of an architectural home with our branding over the top. Preferably translucent.
The image must suit the shape of the google forms image, which is an elongated rectangle
#003d5d - brand colour

Target Market(s)

residential home owners, high end architectural homes

Industry/Entity Type

Residential construction

Colors
0054AA
0677BA
7BADD7
CADEEF
E8F1F8

Requirements
Must have
• our branding and a photo of an architectural home in the background

```html
<!DOCTYPE html>
<html lang="en">
<head>
<meta charset="utf-8">
<title>Velmore Builders – Client Enquiry Form Header</title>
<link href="https://fonts.googleapis.com/css2?family=Montserrat:wght@600&family=Roboto:wght@400;500&display=swap" rel="stylesheet">
<style>
  :root{
    --stage:#a0a0a0;
    --page:#e1eee0;
    --bar:#ffffff;
    --card:#ffffff;
    --card-edge:#dadce0;
    --brand:#003d5d;
    --accent:#3a8d3e;
    --focus:#4a7fd0;
    --ink:#202124;
    --muted:#5f6368;
    --hint:#70757a;
    --required:#d93025;
    --rule:#c4c7c5;
  }
  *{box-sizing:border-box;margin:0;padding:0}
  html,body{width:1200px;height:820px;overflow:hidden}
  body{background:var(--stage);position:relative;font-family:'Roboto',Arial,sans-serif;color:var(--ink)}

  .form-screen{position:absolute;top:66px;width:530px;height:688px;background:var(--page)}
  .form-screen--autumn{left:48.5px}
  .form-screen--harbour{left:621px}

  .tab-bar{position:absolute;left:0;top:0;width:100%;height:24.5px;background:var(--bar);box-shadow:0 1px 0 rgba(0,0,0,.06)}
  .tab{position:absolute;top:7px;font-size:7.8px;font-weight:500;color:var(--ink);transform:translateX(-50%);white-space:nowrap}
  .tab--active{color:var(--accent)}
  .tab-underline{position:absolute;left:187.5px;bottom:0;width:47px;height:2px;background:var(--accent);border-radius:2px 2px 0 0}

  .header-banner{position:absolute;left:48px;top:31.5px;width:419px;height:104px;border-radius:4px;overflow:hidden;background:var(--brand)}
  .header-banner svg{position:absolute;inset:0}
  .brand-name{position:absolute;left:36.5px;top:37px;font-family:'Montserrat',Arial,sans-serif;font-weight:600;font-size:26px;letter-spacing:.5px;color:#ffffff;white-space:nowrap;line-height:1}

  .card{position:absolute;left:48px;width:418px;background:var(--card);border:1px solid var(--card-edge);border-radius:4px}
  .card--focused{border-left:3px solid var(--focus)}
  .card--title{top:143.5px;height:96px;overflow:hidden}
  .card--title::before{content:"";position:absolute;left:-3px;right:-1px;top:-1px;height:5px;background:var(--accent)}
  .form-title{position:absolute;left:13px;top:18.5px;font-size:17.5px;font-weight:400;color:var(--ink)}
  .title-rule{position:absolute;left:13px;top:42px;width:391px;height:1.5px;background:var(--accent)}
  .format-tools{position:absolute;left:14px;top:45px;display:flex;gap:1.7px}
  .format-tool{width:20px;height:20px;display:flex;align-items:center;justify-content:center;border-radius:3px}
  .format-tool--on{background:#e8eaed}
  .form-description{position:absolute;left:13px;top:70.5px;font-size:7.8px;color:var(--muted)}
  .description-rule{position:absolute;left:13px;top:82px;width:391px;height:1px;background:#e0e0e0}

  .card--question{height:74px}
  .question-label{position:absolute;left:13px;top:13px;font-size:9.3px;color:var(--ink)}
  .required{color:var(--required);margin-left:2px;font-size:9px;vertical-align:2px}
  .answer-hint{position:absolute;left:13px;top:38.5px;font-size:7.8px;color:var(--hint);letter-spacing:.1px}
  .answer-rule{position:absolute;left:13px;top:51.5px;height:0;border-top:1px dotted var(--rule)}
  .answer-rule--short{width:196px}
  .answer-rule--long{width:333px}
  .card--focused .question-label,.card--focused .answer-hint,.card--focused .answer-rule{left:11px}

  .side-toolbar{position:absolute;left:473px;top:143.5px;width:26px;height:137px;background:var(--card);border:1px solid var(--card-edge);border-radius:4px;box-shadow:0 1px 2px rgba(0,0,0,.12)}
  .side-toolbar svg{position:absolute;left:5px;width:14px;height:14px}
</style>
</head>
<body>

<section class="form-screen form-screen--autumn">
  <nav class="tab-bar">
    <span class="tab tab--active" style="left:210px">Questions</span>
    <span class="tab" style="left:260px">Responses</span>
    <span class="tab" style="left:306.5px">Settings</span>
    <span class="tab-underline"></span>
  </nav>

  <div class="header-banner">
    <svg width="419" height="104" viewBox="0 0 419 104">
      <defs>
        <linearGradient id="autumnTones" x1="0" y1="0" x2="1" y2="1">
          <stop offset="0" stop-color="#b98a3c"/>
          <stop offset=".35" stop-color="#d9a94a"/>
          <stop offset=".7" stop-color="#8a6a3a"/>
          <stop offset="1" stop-color="#c9b27a"/>
        </linearGradient>
      </defs>
      <polygon points="161,0 419,0 419,104 167,104 130,52" fill="url(#autumnTones)" role="img" aria-label="Photo of a timber-clad architectural home beside water among autumn trees"/>
    </svg>
    <span class="brand-name">Velmore Builders</span>
  </div>

  <div class="card card--title card--focused">
    <h1 class="form-title">Contact information</h1>
    <span class="title-rule"></span>
    <div class="format-tools">
      <span class="format-tool format-tool--on"><svg width="10" height="10" viewBox="0 0 10 10"><text x="5" y="8.6" text-anchor="middle" font-family="Roboto,Arial,sans-serif" font-weight="700" font-size="10" fill="#202124">B</text></svg></span>
      <span class="format-tool"><svg width="10" height="10" viewBox="0 0 10 10"><path d="M4 1.5h4.5M1.5 8.5h4.5M6.3 1.5 3.7 8.5" stroke="#444" stroke-width="1.4" fill="none"/></svg></span>
      <span class="format-tool"><svg width="10" height="11" viewBox="0 0 10 11"><path d="M2.2 1v4a2.8 2.8 0 0 0 5.6 0V1M1.5 10h7" stroke="#444" stroke-width="1.3" fill="none"/></svg></span>
      <span class="format-tool"><svg width="12" height="8" viewBox="0 0 12 8"><path d="M5 1.5H3a2.5 2.5 0 0 0 0 5h2M7 1.5h2a2.5 2.5 0 0 1 0 5H7M3.8 4h4.4" stroke="#444" stroke-width="1.2" fill="none"/></svg></span>
      <span class="format-tool"><svg width="11" height="10" viewBox="0 0 11 10"><path d="M2 1.5h7M5.5 1.5 4 8.5M1.5 1 9.5 9.5" stroke="#444" stroke-width="1.2" fill="none"/></svg></span>
    </div>
    <p class="form-description">Form description</p>
    <span class="description-rule"></span>
  </div>

  <div class="card card--question card--focused" style="top:246.7px">
    <p class="question-label">Name<span class="required">*</span></p>
    <p class="answer-hint">Short answer text</p><span class="answer-rule answer-rule--short"></span>
  </div>
  <div class="card card--question" style="top:328px">
    <p class="question-label">Email<span class="required">*</span></p>
    <p class="answer-hint">Short answer text</p><span class="answer-rule answer-rule--short"></span>
  </div>
  <div class="card card--question" style="top:409px">
    <p class="question-label">Address<span class="required">*</span></p>
    <p class="answer-hint">Long answer text</p><span class="answer-rule answer-rule--long"></span>
  </div>
  <div class="card card--question" style="top:490px">
    <p class="question-label">Phone number</p>
    <p class="answer-hint">Short answer text</p><span class="answer-rule answer-rule--short"></span>
  </div>
  <div class="card card--question" style="top:572px">
    <p class="question-label">Comments</p>
    <p class="answer-hint">Long answer text</p><span class="answer-rule answer-rule--long"></span>
  </div>

  <aside class="side-toolbar">
    <svg style="top:7.5px" viewBox="0 0 14 14"><circle cx="7" cy="7" r="5.5" fill="none" stroke="#5f6368" stroke-width="1.2"/><path d="M7 4v6M4 7h6" stroke="#5f6368" stroke-width="1.2"/></svg>
    <svg style="top:29px" viewBox="0 0 14 14"><path d="M3 1.5h5l3 3v8H3v-4M3 4.5V1.5M1 7h6M5 5l2 2-2 2" fill="none" stroke="#5f6368" stroke-width="1.1"/></svg>
    <svg style="top:51px" viewBox="0 0 14 14"><path d="M1 3h7M4.5 3v9M7.5 6.5h5.5M10.2 6.5V12" stroke="#5f6368" stroke-width="1.5" fill="none"/></svg>
    <svg style="top:72.5px" viewBox="0 0 14 14"><rect x="2" y="2" width="10" height="10" rx="1" fill="none" stroke="#5f6368" stroke-width="1.1"/><path d="M3.5 10.5l2.5-3 2 2 1.5-1.5 1.5 2.5z" fill="#5f6368"/></svg>
    <svg style="top:94px" viewBox="0 0 14 14"><rect x="1.5" y="3" width="11" height="8.5" rx="1" fill="none" stroke="#5f6368" stroke-width="1.1"/><path d="M6 5.3v4l3-2z" fill="#5f6368"/></svg>
    <svg style="top:116px" viewBox="0 0 14 14"><rect x="2" y="2" width="10" height="4.2" fill="none" stroke="#5f6368" stroke-width="1.1"/><rect x="2" y="7.8" width="10" height="4.2" fill="none" stroke="#5f6368" stroke-width="1.1"/></svg>
  </aside>
</section>

<section class="form-screen form-screen--harbour">
  <nav class="tab-bar">
    <span class="tab tab--active" style="left:210px">Questions</span>
    <span class="tab" style="left:260px">Responses</span>
    <span class="tab" style="left:306.5px">Settings</span>
    <span class="tab-underline"></span>
  </nav>

  <div class="header-banner">
    <svg width="419" height="104" viewBox="0 0 419 104">
      <defs>
        <linearGradient id="harbourTones" x1="0" y1="0" x2="1" y2="1">
          <stop offset="0" stop-color="#6a6fa8"/>
          <stop offset=".35" stop-color="#b9a6cf"/>
          <stop offset=".65" stop-color="#5b5c98"/>
          <stop offset=".85" stop-color="#e0a47a"/>
          <stop offset="1" stop-color="#8a88c0"/>
        </linearGradient>
      </defs>
      <polygon points="167,0 419,0 419,104 172,104 132,52" fill="url(#harbourTones)" role="img" aria-label="Photo of an angular glass waterfront building at sunset beside a harbour"/>
    </svg>
    <span class="brand-name">Velmore Builders</span>
  </div>

  <div class="card card--title card--focused">
    <h1 class="form-title">Contact information</h1>
    <span class="title-rule"></span>
    <div class="format-tools">
      <span class="format-tool format-tool--on"><svg width="10" height="10" viewBox="0 0 10 10"><text x="5" y="8.6" text-anchor="middle" font-family="Roboto,Arial,sans-serif" font-weight="700" font-size="10" fill="#202124">B</text></svg></span>
      <span class="format-tool"><svg width="10" height="10" viewBox="0 0 10 10"><path d="M4 1.5h4.5M1.5 8.5h4.5M6.3 1.5 3.7 8.5" stroke="#444" stroke-width="1.4" fill="none"/></svg></span>
      <span class="format-tool"><svg width="10" height="11" viewBox="0 0 10 11"><path d="M2.2 1v4a2.8 2.8 0 0 0 5.6 0V1M1.5 10h7" stroke="#444" stroke-width="1.3" fill="none"/></svg></span>
      <span class="format-tool"><svg width="12" height="8" viewBox="0 0 12 8"><path d="M5 1.5H3a2.5 2.5 0 0 0 0 5h2M7 1.5h2a2.5 2.5 0 0 1 0 5H7M3.8 4h4.4" stroke="#444" stroke-width="1.2" fill="none"/></svg></span>
      <span class="format-tool"><svg width="11" height="10" viewBox="0 0 11 10"><path d="M2 1.5h7M5.5 1.5 4 8.5M1.5 1 9.5 9.5" stroke="#444" stroke-width="1.2" fill="none"/></svg></span>
    </div>
    <p class="form-description">Form description</p>
    <span class="description-rule"></span>
  </div>

  <div class="card card--question card--focused" style="top:246.7px">
    <p class="question-label">Name<span class="required">*</span></p>
    <p class="answer-hint">Short answer text</p><span class="answer-rule answer-rule--short"></span>
  </div>
  <div class="card card--question" style="top:328px">
    <p class="question-label">Email<span class="required">*</span></p>
    <p class="answer-hint">Short answer text</p><span class="answer-rule answer-rule--short"></span>
  </div>
  <div class="card card--question" style="top:409px">
    <p class="question-label">Address<span class="required">*</span></p>
    <p class="answer-hint">Long answer text</p><span class="answer-rule answer-rule--long"></span>
  </div>
  <div class="card card--question" style="top:490px">
    <p class="question-label">Phone number</p>
    <p class="answer-hint">Short answer text</p><span class="answer-rule answer-rule--short"></span>
  </div>
  <div class="card card--question" style="top:572px">
    <p class="question-label">Comments</p>
    <p class="answer-hint">Long answer text</p><span class="answer-rule answer-rule--long"></span>
  </div>

  <aside class="side-toolbar">
    <svg style="top:7.5px" viewBox="0 0 14 14"><circle cx="7" cy="7" r="5.5" fill="none" stroke="#5f6368" stroke-width="1.2"/><path d="M7 4v6M4 7h6" stroke="#5f6368" stroke-width="1.2"/></svg>
    <svg style="top:29px" viewBox="0 0 14 14"><path d="M3 1.5h5l3 3v8H3v-4M3 4.5V1.5M1 7h6M5 5l2 2-2 2" fill="none" stroke="#5f6368" stroke-width="1.1"/></svg>
    <svg style="top:51px" viewBox="0 0 14 14"><path d="M1 3h7M4.5 3v9M7.5 6.5h5.5M10.2 6.5V12" stroke="#5f6368" stroke-width="1.5" fill="none"/></svg>
    <svg style="top:72.5px" viewBox="0 0 14 14"><rect x="2" y="2" width="10" height="10" rx="1" fill="none" stroke="#5f6368" stroke-width="1.1"/><path d="M3.5 10.5l2.5-3 2 2 1.5-1.5 1.5 2.5z" fill="#5f6368"/></svg>
    <svg style="top:94px" viewBox="0 0 14 14"><rect x="1.5" y="3" width="11" height="8.5" rx="1" fill="none" stroke="#5f6368" stroke-width="1.1"/><path d="M6 5.3v4l3-2z" fill="#5f6368"/></svg>
    <svg style="top:116px" viewBox="0 0 14 14"><rect x="2" y="2" width="10" height="4.2" fill="none" stroke="#5f6368" stroke-width="1.1"/><rect x="2" y="7.8" width="10" height="4.2" fill="none" stroke="#5f6368" stroke-width="1.1"/></svg>
  </aside>
</section>

</body>
</html>
```